Brindovalle Business cards

Dear team, I need to get the design file to suit it to our team. The focus of the business card is the Automotive Market and the design must be in black colour and the logo must be in glossy black. On the front of the card I need to get the following info:

- Name and Surname
- Title
- eMail
- Phone Number
- Skype account
- domain address

```html
<!DOCTYPE html>
<html lang="en">
<head>
<meta charset="utf-8">
<title>Brindovalle Business Cards</title>
<link href="https://fonts.googleapis.com/css2?family=Poppins:wght@400;500;700&display=swap" rel="stylesheet">
<style>
  :root {
    --bg: #2e2926;
    --card: #161616;
    --card-edge: #0c0c0c;
    --red: #e8252f;
    --white: #ffffff;
    --grey: #d9d9d9;
  }
  * { margin: 0; padding: 0; box-sizing: border-box; }
  html, body { width: 1200px; height: 716px; overflow: hidden; }
  body {
    background: var(--bg);
    font-family: "Poppins", sans-serif;
    display: flex;
    align-items: center;
    justify-content: center;
    gap: 56px;
  }
  .card {
    position: relative;
    width: 520px;
    height: 298px;
    background: var(--card);
    border-radius: 6px;
    overflow: hidden;
    box-shadow: 0 14px 30px rgba(0,0,0,.45);
  }
  .card-back { border-bottom: 5px solid var(--red); }
  .back-pattern {
    position: absolute;
    inset: 0;
    background: linear-gradient(100deg, #0d0d0d 0%, #151515 38%, #4a4a4a 60%, #3a3a3a 80%, #9a9a9a 100%);
    opacity: .85;
  }
  .brand {
    position: absolute;
    top: 40px;
    left: 0; right: 0;
    display: flex;
    justify-content: center;
    align-items: center;
    gap: 12px;
  }
  .brand-dot {
    width: 30px; height: 30px;
    background: var(--red);
    border-radius: 50%;
  }
  .brand-name {
    color: var(--white);
    font-weight: 700;
    font-size: 38px;
    letter-spacing: -0.5px;
  }
  .person {
    position: absolute;
    top: 108px;
    left: 0; right: 0;
    text-align: center;
  }
  .name-row {
    display: flex;
    align-items: center;
    justify-content: center;
    gap: 14px;
  }
  .rule { height: 1px; width: 110px; background: var(--red); }
  .rule-left { background: linear-gradient(90deg, transparent, var(--red)); }
  .rule-right { background: linear-gradient(90deg, var(--red), transparent); }
  .person-name {
    color: var(--red);
    font-weight: 700;
    font-size: 24px;
    letter-spacing: .5px;
    text-transform: uppercase;
  }
  .person-title {
    color: var(--white);
    font-size: 13px;
    margin-top: -2px;
  }
  .contacts {
    position: absolute;
    top: 170px;
    left: 0; right: 0;
    list-style: none;
    color: var(--white);
    font-size: 13px;
    line-height: 19px;
    text-align: center;
  }
  .contacts li { display: flex; justify-content: center; align-items: center; gap: 5px; }
  .contacts svg { width: 11px; height: 11px; fill: var(--red); flex: none; }
  .skype-dot { width: 9px; height: 9px; border-radius: 50%; background: var(--red); margin-left: 8px; }
  .band {
    position: absolute;
    left: 0; right: 0;
    top: 246px;
    height: 24px;
    background: var(--red);
  }
  .band-mark {
    position: absolute;
    left: 118px;
    top: 237px;
    width: 42px; height: 42px;
    border-radius: 50%;
    background: var(--white);
    border: 8px solid var(--card);
  }
</style>
</head>
<body>
  <section class="card card-back">
    <div class="back-pattern" role="img" aria-label="Repeating glossy black brand-mark pattern with one red accent mark"></div>
  </section>

  <section class="card card-front">
    <div class="brand">
      <span class="brand-dot"></span>
      <span class="brand-name">Brindovalle.com</span>
    </div>

    <div class="person">
      <div class="name-row">
        <span class="rule rule-left"></span>
        <h1 class="person-name">Darel Quinby</h1>
        <span class="rule rule-right"></span>
      </div>
      <p class="person-title">Director</p>
    </div>

    <ul class="contacts">
      <li>
        <svg viewBox="0 0 24 24" aria-hidden="true"><path d="M6.6 10.8a15 15 0 0 0 6.6 6.6l2.2-2.2c.3-.3.7-.4 1-.2 1.1.4 2.3.6 3.6.6.6 0 1 .4 1 1V20c0 .6-.4 1-1 1A17 17 0 0 1 3 4c0-.6.4-1 1-1h3.5c.6 0 1 .4 1 1 0 1.3.2 2.5.6 3.6.1.3 0 .7-.2 1z"/></svg>
        918-555-0142
        <span class="skype-dot"></span> brindovalle
      </li>
      <li>
        <svg viewBox="0 0 24 24" aria-hidden="true"><path d="M2 5h20v14H2z M2 5l10 8 10-8" stroke="#161616" stroke-width="1.5"/></svg>
        info@brindovalle.com
      </li>
      <li>
        <svg viewBox="0 0 24 24" aria-hidden="true"><path d="M12 2a7 7 0 0 0-7 7c0 5 7 13 7 13s7-8 7-13a7 7 0 0 0-7-7zm0 9.5A2.5 2.5 0 1 1 12 6.5a2.5 2.5 0 0 1 0 5z"/></svg>
        2280 W Calloway, Fenmore, Oklahoma 74190
      </li>
    </ul>

    <div class="band"></div>
    <span class="band-mark"></span>
  </section>
</body>
</html>
```